BrindleStaffing Business Card Design

We are a staffing company finding positions for dedicated nurses and physicians.

Target Market(s)

Business Professionals

Industry/Entity Type

Staffing

Contact Information for Business Card

Gordon Pratley
Chairman
417 39th Avenue South
SAINT PETERSBURG FL 33712
813-555-4172 Mobile
813-555-8036 Fax
gpratley@brindlestaffing.com
www.brindlestaffing.com

Font styles to use
Sans Serif

Colors
fbee3e
f04a50
f37122

Requirements
Must have
• Logo Attached, see colors below. We'd like to see Yellow, Orange and Red.

```html
<!DOCTYPE html>
<html lang="en">
<head>
<meta charset="utf-8">
<title>BrindleStaffing Business Card</title>
<link href="https://fonts.googleapis.com/css2?family=Open+Sans:wght@400;700&family=Cormorant+Garamond:ital,wght@1,500&display=swap" rel="stylesheet">
<style>
  :root {
    --backdrop: #3a3a3a;
    --card: #141414;
    --card-edge: #1f1f1f;
    --brand-orange: #f37122;
    --brand-red: #f04a50;
    --brand-yellow: #fbee3e;
    --ink: #ffffff;
  }
  * { margin: 0; padding: 0; box-sizing: border-box; }
  html, body { width: 1200px; height: 717px; overflow: hidden; }
  body {
    background: var(--backdrop);
    font-family: "Open Sans", sans-serif;
    position: relative;
  }
  .card {
    position: absolute;
    top: 215px;
    width: 500px;
    height: 286px;
    background: linear-gradient(160deg, var(--card-edge), var(--card));
    border-radius: 4px;
    box-shadow: 0 14px 30px rgba(0,0,0,.45);
    overflow: hidden;
  }
  .card--front { left: 60px; }
  .card--back { left: 640px; }

  .wordmark {
    position: absolute;
    font-weight: 700;
    color: var(--brand-orange);
    letter-spacing: -0.5px;
    line-height: 1;
    white-space: nowrap;
  }
  .card--front .wordmark { left: 80px; top: 122px; font-size: 46px; }
  .card--back .wordmark { left: 40px; top: 40px; font-size: 36px; }

  .brand-square {
    position: absolute;
    background: var(--brand-yellow);
  }
  .card--front .brand-square { left: 232px; top: 44px; width: 56px; height: 56px; }
  .card--back .brand-square { right: 36px; bottom: 40px; width: 60px; height: 60px; }

  .holder-name {
    position: absolute;
    left: 44px; top: 92px;
    font-family: "Cormorant Garamond", serif;
    font-style: italic;
    font-weight: 500;
    font-size: 26px;
    color: var(--brand-red);
    white-space: nowrap;
  }
  .contact-list {
    position: absolute;
    left: 40px; top: 144px;
    list-style: none;
    font-size: 13px;
    color: var(--ink);
    line-height: 21px;
  }
  .contact-list li { display: flex; align-items: center; gap: 8px; white-space: nowrap; }
  .contact-icon {
    width: 13px; height: 13px;
    flex: none;
  }
</style>
</head>
<body>
  <section class="card card--front">
    <div class="brand-square"></div>
    <div class="wordmark">BrindleStaffing</div>
  </section>

  <section class="card card--back">
    <div class="wordmark">BrindleStaffing</div>
    <div class="holder-name">Gordon Pratley</div>
    <ul class="contact-list">
      <li>
        <svg class="contact-icon" viewBox="0 0 13 13" aria-hidden="true"><rect width="13" height="13" rx="2" fill="#f04a50"/><path d="M4 3 C3 5 5 9 9 10 L10 8.5 L8.5 7.5 L7.6 8.3 C6.5 7.8 5.3 6.6 4.8 5.4 L5.6 4.5 L4.6 3 Z" fill="#141414"/></svg>
        813-555-4172
      </li>
      <li>
        <svg class="contact-icon" viewBox="0 0 13 13" aria-hidden="true"><rect width="13" height="13" rx="2" fill="#f04a50"/><rect x="2.5" y="4" width="8" height="5.5" fill="none" stroke="#141414" stroke-width="1"/><path d="M2.5 4 L6.5 7 L10.5 4" fill="none" stroke="#141414" stroke-width="1"/></svg>
        gpratley@brindlestaffing.com
      </li>
      <li>
        <svg class="contact-icon" viewBox="0 0 13 13" aria-hidden="true"><rect width="13" height="13" rx="2" fill="#f04a50"/><circle cx="6.5" cy="6.5" r="3.6" fill="none" stroke="#141414" stroke-width="1"/><path d="M2.9 6.5 H10.1 M6.5 2.9 V10.1" stroke="#141414" stroke-width="0.8"/></svg>
        www.brindlestaffing.com
      </li>
      <li>
        <svg class="contact-icon" viewBox="0 0 13 13" aria-hidden="true"><rect width="13" height="13" rx="2" fill="#f04a50"/><path d="M6.5 2.5 C4.8 2.5 3.8 3.7 3.8 5 C3.8 7 6.5 10.5 6.5 10.5 C6.5 10.5 9.2 7 9.2 5 C9.2 3.7 8.2 2.5 6.5 2.5 Z" fill="#141414"/><circle cx="6.5" cy="5" r="1" fill="#f04a50"/></svg>
        417 39th Avenue South, SAINT PETERSBURG FL 33712
      </li>
    </ul>
    <div class="brand-square"></div>
  </section>
</body>
</html>
```